Buch-/eBook-Cover für Sachbuch gesucht
Zielgruppe
We're selfpublishing nonfiction books. Interested are adults - mostly man (age range: 25-50) - who want to learn more about leadership at their workplaces.
Aufgabenstellung
The design should be clean and simple, title easy to read, good color contrast (the cover has to stand out from an white background).

```html
<!DOCTYPE html>
<html lang="en">
<head>
<meta charset="utf-8">
<title>Leadership – Book Cover</title>
<link rel="stylesheet" href="https://fonts.googleapis.com/css2?family=Bebas+Neue&family=Oswald:wght@600&family=Poppins:wght@400&display=swap">
<style>
  :root {
    --stage: #333333;
    --sand: #ecd0a5;
    --paper: #efefef;
    --ink: #333333;
  }
  html, body {
    margin: 0;
    padding: 0;
    width: 1074px;
    height: 1200px;
    overflow: hidden;
    background: var(--stage);
  }
  .canvas {
    position: relative;
    width: 1074px;
    height: 1200px;
    background: var(--stage);
  }
  .cover {
    position: absolute;
    left: 216px;
    top: 147px;
    width: 641px;
    height: 905px;
    background: var(--sand);
    overflow: hidden;
  }
  .cover__corners {
    position: absolute;
    inset: 0;
    width: 641px;
    height: 905px;
  }
  .cover__corners polygon { fill: var(--paper); }
  .rule {
    position: absolute;
    height: 3px;
    background: var(--ink);
  }
  .rule--top { left: 86px; width: 470px; top: 261px; }
  .rule--mid { left: 276px; width: 275px; top: 369px; }
  .title {
    position: absolute;
    right: 87px;
    top: 277px;
    margin: 0;
    margin-right: -16px;
    font-family: "Bebas Neue", "Oswald", sans-serif;
    font-weight: 400;
    font-size: 80px;
    line-height: 1;
    letter-spacing: 16px;
    color: var(--ink);
    white-space: nowrap;
  }
  .subtitle {
    position: absolute;
    right: 90px;
    top: 381px;
    margin: 0;
    font-family: "Poppins", sans-serif;
    font-weight: 400;
    font-size: 47px;
    line-height: 55.7px;
    color: var(--ink);
    text-align: right;
    letter-spacing: -1px;
  }
  .subtitle span { display: block; }
  .author {
    position: absolute;
    left: 73px;
    top: 853px;
    margin: 0;
    font-family: "Oswald", sans-serif;
    font-weight: 600;
    font-size: 24px;
    line-height: 1;
    letter-spacing: -0.3px;
    transform: scaleX(0.86);
    transform-origin: left center;
    color: var(--ink);
    white-space: nowrap;
  }
</style>
</head>
<body>
  <main class="canvas">
    <article class="cover">
      <svg class="cover__corners" viewBox="0 0 641 905" aria-hidden="true">
        <polygon points="0,0 309,0 0,253"/>
        <polygon points="641,741 641,905 438,905"/>
      </svg>
      <div class="rule rule--top"></div>
      <h1 class="title">LEADERSHIP</h1>
      <div class="rule rule--mid"></div>
      <h2 class="subtitle">
        <span>FOSTERING</span>
        <span>GROWTH</span>
        <span>AND</span>
        <span>INSPIRING</span>
        <span>EXCELLENCE</span>
      </h2>
      <p class="author">DANIEL WHITMORE</p>
    </article>
  </main>
</body>
</html>
```